Payment company requires web design

We need a web design for a new company based in Singapore.

The company focuses on providing 2 key products: 1) an alternative payment option (i.e. like quib or trelloquin options) on the traditional checkout process 2) a replacement/outsource of a merchants payment page. Key in the UX flow is a end customer dashboard that manages all payments.

We look to provide a simple, fluid and easy to use payment process. The dashboard is minimalistic that allows easy navigation, review of transactions and all available options through gamification.

The final design should communicate ease of use, flexibility and transparency.

Target Market(s)

The value is for the merchant - retail/travel/insurance companies. However its the merchant's end customers that are the target and who the UX is built for.

Industry/Entity Type

It Company

Logo Text

zelnar

Number of Pages Required

5+ page

Colors
ec1f27

Requirements
Must have
• 7 pages mimicking UX flow
• payment page * 2 - 1) alternative payment type 2) outsource of merchants payment page to our business
• our landing page
• end customer verification page
• end customer registration
• customer dashboard
• UX flow in attached file
Nice to have
• open to ideas
• have asked for the logo to be added
• logo to have the colour red (chinese for prosperity)
• the company is all about flexibility, transparency in personal finance management with the option of instalment payments

```html
<!DOCTYPE html>
<html lang="en">
<head>
<meta charset="utf-8">
<title>Zelnar — Payment Processing</title>
<link rel="stylesheet" href="https://fonts.googleapis.com/css2?family=Open+Sans:wght@400;600;700&display=swap">
<style>
:root{
  --red:#ec1f27;
  --red-deep:#d3151c;
  --ink:#333;
  --muted:#777;
  --line:#d8d8d8;
  --band:#f2f2f2;
  --dark:#555;
  --white:#fff;
}
*{box-sizing:border-box;margin:0;padding:0}
html,body{width:684px;height:1200px;overflow:hidden;background:var(--white)}
body{position:relative;font-family:"Open Sans",sans-serif;color:var(--ink)}

/* header */
.site-header{position:absolute;left:0;top:0;width:684px;height:59px;background:var(--white);box-shadow:0 2px 3px rgba(0,0,0,.12);z-index:2}
.brand{position:absolute;left:50px;top:17px;font-size:22px;font-weight:700;letter-spacing:3px;color:var(--red);line-height:1}
.nav{position:absolute;left:214px;top:22px;display:flex;align-items:center;font-size:8px;color:var(--ink);text-transform:uppercase}
.nav a{color:inherit;text-decoration:none;margin-right:18px}
.nav .active{color:var(--red);border:1px solid var(--red);border-radius:10px;padding:3px 8px;margin-right:10px}
.nav .register{background:var(--dark);color:var(--white);border-radius:9px;padding:3px 9px;margin-right:12px;font-weight:600}

/* hero */
.hero{position:absolute;left:0;top:59px;width:684px;height:306px;background:linear-gradient(90deg,#eeeeec 0%,#d9d4cf 30%,#ece8e2 60%,#f1ece4 100%)}
.hero-title{position:absolute;left:402px;top:142px;font-size:21px;color:var(--red);letter-spacing:.5px}
.hero-sub{position:absolute;left:402px;top:167px;font-size:12px;color:var(--ink);letter-spacing:.4px}
.slider-arrows{position:absolute;left:594px;top:196px;display:flex;gap:3px}
.slider-arrows span{width:16px;height:16px;border-radius:50%;background:#888;color:#fff;font-size:10px;line-height:15px;text-align:center}

/* features */
.section-title{position:absolute;left:0;width:684px;text-align:center;font-size:14.5px;color:var(--red);letter-spacing:.3px;font-weight:400}
.feature{position:absolute;top:447px;width:180px;height:56px}
.feature-icon{position:absolute;left:0;top:0;width:54px;height:54px;border:1px solid #444;border-radius:50%;display:flex;align-items:center;justify-content:center}
.feature h3{position:absolute;left:62px;top:1px;font-size:9.5px;font-weight:400;text-transform:uppercase;color:var(--ink)}
.feature p{position:absolute;left:62px;top:20px;width:118px;font-size:6.4px;line-height:10.5px;color:var(--muted)}

/* what we do */
.about{position:absolute;left:0;top:543px;width:684px;height:208px;background:var(--band)}
.about h2{position:absolute;left:50px;top:37px;font-size:14.5px;font-weight:400;color:var(--red)}
.about p{position:absolute;left:50px;top:62px;width:274px;font-size:6.4px;line-height:13px;color:#444;text-align:justify}
.btn-outline{position:absolute;left:50px;top:156px;border:1px solid var(--red);border-radius:10px;color:var(--red);font-size:6px;line-height:8px;padding:5px 10px;text-transform:uppercase}
.video{position:absolute;left:343px;top:20px;width:293px;height:164px;background:var(--white);border:1px solid #ccc;box-shadow:0 0 3px rgba(0,0,0,.2);padding:3px}
.video-media{width:100%;height:100%;background:linear-gradient(120deg,#6f6a63 0%,#c9c3ba 40%,#ecebe8 70%,#b5b9bf 100%);position:relative}
.play{position:absolute;left:127px;top:62px;width:33px;height:33px;border-radius:50%;background:rgba(40,40,40,.75)}

/* reviews */
.review{position:absolute;top:830px;width:280px;height:70px}
.avatar{position:absolute;left:0;top:3px;width:64px;height:64px;border-radius:50%;border:1px solid #ccc;background:linear-gradient(180deg,#d8dde2,#a9b6c3)}
.avatar.alt{background:linear-gradient(180deg,#e6ddd2,#b49a80)}
.stars{position:absolute;left:76px;top:-3px;font-size:12px;letter-spacing:-.5px;color:#f3c315}
.stars .off{color:#e2c95a}
.quote{position:absolute;left:76px;top:15px;width:200px;font-size:6.5px;line-height:12.5px;color:#444}
.quote b{color:var(--red);font-size:9px;font-weight:700}
.author{position:absolute;left:76px;top:53px;font-size:6.5px;color:var(--red)}

/* promo band */
.promo{position:absolute;left:0;top:929px;width:684px;height:106px;background:linear-gradient(115deg,#e3262d 0%,var(--red) 35%,#d7161d 60%,#ef3a40 80%,var(--red-deep) 100%)}
.promo h2{position:absolute;left:50px;top:27px;font-size:13.5px;font-weight:600;color:var(--white);letter-spacing:.3px}
.promo p{position:absolute;left:50px;top:49px;width:440px;font-size:8.2px;line-height:14px;color:var(--white)}
.btn-light{position:absolute;left:515px;top:48px;width:97px;height:29px;background:#f4f4f4;border:1px solid #ddd;color:#444;font-size:10px;text-align:center;line-height:28px}

/* footer */
.footer-brand{position:absolute;left:55px;top:1097px;font-size:20px;font-weight:700;letter-spacing:3px;color:#6a6a6a}
.footer-col{position:absolute;top:1068px}
.footer-col h4{font-size:7.8px;font-weight:400;color:var(--ink);text-transform:uppercase;margin-bottom:12px}
.footer-col p{font-size:6px;line-height:12.5px;color:var(--muted)}
.newsletter{display:flex;margin-top:7px}
.newsletter span{width:84px;height:18px;border:1px solid #ccc;font-size:6px;color:var(--muted);line-height:16px;padding-left:5px}
.newsletter b{height:18px;background:var(--red);color:#fff;font-size:6.5px;font-weight:400;line-height:18px;padding:0 5px}
.social{display:flex;gap:6px;font-size:7px;color:#444}
.social span{display:flex;align-items:center;gap:2px}
.social i{display:inline-block;width:5px;height:5px;background:#444}
.footer-rule{position:absolute;left:48px;top:1164px;width:583px;height:1px;background:var(--line)}
.copyright{position:absolute;left:0;top:1180px;width:684px;text-align:center;font-size:6.8px;color:#444}
</style>
</head>
<body>

<header class="site-header">
  <div class="brand">ZELNAR</div>
  <nav class="nav">
    <a class="active">&#8962; Home</a>
    <a>About us</a>
    <a>Services</a>
    <a>Projects</a>
    <a>Blog</a>
    <a>Contacts</a>
    <a class="register">Registration</a>
    <svg width="10" height="10" viewBox="0 0 10 10"><circle cx="4" cy="4" r="3" fill="none" stroke="#ec1f27" stroke-width="1.6"/><line x1="6.2" y1="6.2" x2="9" y2="9" stroke="#ec1f27" stroke-width="1.8"/></svg>
  </nav>
</header>

<section class="hero" role="img" aria-label="Smiling woman holding a bank card while shopping on a laptop">
  <div class="hero-title">PAYMENT PROCESSING</div>
  <div class="hero-sub">Neque porro quisquam est qui dolorem</div>
  <div class="slider-arrows"><span>&#8249;</span><span>&#8250;</span></div>
</section>

<h2 class="section-title" style="top:403px">PAYMENT PROCESSING</h2>

<div class="feature" style="left:51px">
  <div class="feature-icon">
    <svg width="20" height="18" viewBox="0 0 20 18"><rect x="1" y="1" width="18" height="12" fill="none" stroke="#ec1f27" stroke-width="2"/><rect x="3" y="3" width="14" height="8" fill="#ec1f27"/><rect x="8" y="13" width="4" height="3" fill="#ec1f27"/><rect x="5" y="16" width="10" height="2" fill="#ec1f27"/></svg>
  </div>
  <h3>Sign in</h3>
  <p>It was popularised in the 1960s with the release of Typeline sheets containing Lorem Ipsum passages.</p>
</div>

<div class="feature" style="left:254px">
  <div class="feature-icon">
    <svg width="22" height="18" viewBox="0 0 22 18"><circle cx="11" cy="4" r="3.2" fill="#ec1f27"/><circle cx="4.5" cy="6" r="2.5" fill="#ec1f27"/><circle cx="17.5" cy="6" r="2.5" fill="#ec1f27"/><path d="M6 18v-5a5 5 0 0 1 10 0v5z" fill="#ec1f27"/><path d="M0 16v-3a4 4 0 0 1 6-3.4V16z" fill="#ec1f27"/><path d="M22 16v-3a4 4 0 0 0-6-3.4V16z" fill="#ec1f27"/></svg>
  </div>
  <h3>Merchant</h3>
  <p>It was popularised in the 1960s with the release of Typeline sheets containing Lorem Ipsum passages.</p>
</div>

<div class="feature" style="left:453px">
  <div class="feature-icon">
    <svg width="24" height="18" viewBox="0 0 24 18"><rect x="1" y="1" width="22" height="16" rx="2" fill="none" stroke="#ec1f27" stroke-width="2"/><rect x="1" y="5" width="22" height="3" fill="#ec1f27"/><rect x="4" y="12" width="5" height="2" fill="#ec1f27"/><rect x="11" y="12" width="4" height="2" fill="#ec1f27"/></svg>
  </div>
  <h3>Instalment payments</h3>
  <p>It was popularised in the 1960s with the release of Typeline sheets containing Lorem Ipsum passages.</p>
</div>

<section class="about">
  <h2>WHAT WE DO</h2>
  <p>Lorem Ipsum has been the industry's standard dummy text ever since the 1500s, when an unknown printer took a galley of type and scrambled it to make a type specimen book. It has survived not only five centuries, but also the leap into electronic typesetting, remaining essentially unchanged. It was popularised in the 1960s with the release of Typeline sheets containing Lorem Ipsum passages, and more recently with desktop publishing software like Pagewright Studio including versions</p>
  <div class="btn-outline">Pay later &raquo;</div>
  <div class="video">
    <div class="video-media" role="img" aria-label="Hands holding a bank card over a laptop keyboard, video preview">
      <div class="play"><svg width="33" height="33" viewBox="0 0 33 33"><path d="M13 10l10 6.5-10 6.5z" fill="#fff"/></svg></div>
    </div>
  </div>
</section>

<h2 class="section-title" style="top:780px">CUSTOMER REVIEWS</h2>

<div class="review" style="left:50px">
  <div class="avatar" role="img" aria-label="Portrait of customer Mara Lindqvist"></div>
  <div class="stars">★★★<span class="off">★☆</span></div>
  <div class="quote"><b>&ldquo;</b> Lorem Ipsum has been the industry's standard dummy text ever since the 1500s, when an unknown printer took a galley of type and scrambled it to make a type specimen book. <b>&rdquo;</b></div>
  <div class="author">Mara Lindqvist</div>
</div>

<div class="review" style="left:360px">
  <div class="avatar alt" role="img" aria-label="Portrait of customer Theo Brandt"></div>
  <div class="stars">★★★<span class="off">★☆</span></div>
  <div class="quote"><b>&ldquo;</b> Lorem Ipsum has been the industry's standard dummy text ever since the 1500s, when an unknown printer took a galley of type and scrambled it to make a type specimen book. <b>&rdquo;</b></div>
  <div class="author" style="top:55px">Theo Brandt</div>
</div>

<section class="promo">
  <h2>PERSONAL FINANCE MANAGEMENT</h2>
  <p>Lorem Ipsum has been the industry's standard dummy text ever since the 1500s, when an unknown printer took a galley of type and scrambled it to make a type specimen book. It has survived not only five centuries,</p>
  <div class="btn-light">CLICK HERE</div>
</section>

<div class="footer-brand">ZELNAR</div>

<div class="footer-col" style="left:204px">
  <h4>Contact us</h4>
  <p>Address : 12 Harrow Lane, Eastgate<br>Tollford, TF4 2QP<br>Phone : 555-018-2736.<br>Email : hello@zelnar-mail.test</p>
</div>

<div class="footer-col" style="left:369px">
  <h4>Sign up for newsletter</h4>
  <p style="width:118px;line-height:10px">Your about us information would fit here nicely.</p>
  <div class="newsletter"><span>Email address</span><b>Submit</b></div>
</div>

<div class="footer-col" style="left:540px">
  <h4>Follow us out there</h4>
  <div class="social"><span><i></i>Facio</span><span><i></i>Chirpa</span><span><i></i>Linkt</span><span><i></i>Plusly</span></div>
</div>

<div class="footer-rule"></div>
<div class="copyright">Copyright © 2016. All Rights Reserved</div>

</body>
</html>
```